Zielgruppe
Verkauf und Einbau von Fenstern, Haustüren, Rollläden, Raffstore, Markisen, Insektenschutzgitter, Plissees
Aufgabenstellung
Es soll das gleiche Farbschema meines Firmenlogos haben. Grauer Hintergrund, kleine gelbe Akzente und schwarze Schrift

```html
<!DOCTYPE html>
<html lang="de">
<head>
<meta charset="utf-8">
<title>Rahmenwerk – Fenster, Haustüren, Sonnenschutz</title>
<link rel="stylesheet" href="https://fonts.googleapis.com/css2?family=Work+Sans:wght@400;500;600;700&family=Inter:wght@400;500;600&display=swap">
<style>
  :root {
    --backdrop: #ababab;
    --page: #f2f2f2;
    --card: #ffffff;
    --brown-dark: #4a2714;
    --brown: #6e2f1c;
    --heading: #4b2010;
    --yellow: #f2c30f;
    --button: #d2a413;
    --hero-a: #5a3a24;
    --hero-b: #a07a55;
    --hero-c: #2e1d12;
    --text: #555555;
    --white: #ffffff;
    --line: #cfcfcf;
  }
  * { margin: 0; padding: 0; box-sizing: border-box; }
  html, body { width: 1200px; height: 1200px; overflow: hidden; }
  body { background: var(--backdrop); font-family: "Inter", sans-serif; position: relative; }
  .page { position: absolute; left: 179px; top: 44px; width: 842px; height: 1156px; background: var(--page); overflow: hidden; }

  .nav { position: absolute; left: 0; top: 0; width: 100%; height: 53px; background: var(--brown-dark); z-index: 2; }
  .nav a { position: absolute; top: 19px; color: var(--white); font-size: 12px; text-decoration: none; font-family: "Inter", sans-serif; }
  .nav a.active { border-bottom: 1px solid var(--white); padding-bottom: 1px; }

  .hero { position: absolute; left: 0; top: 53px; width: 100%; height: 420px; overflow: hidden;
    background: radial-gradient(ellipse at 40% 40%, var(--hero-b) 0%, var(--hero-a) 45%, var(--hero-c) 100%); }
  .hero-overlay { position: absolute; inset: 0; background: rgba(30,18,10,0.25); }
  .brand { position: absolute; top: 172px; left: 0; width: 100%; text-align: center; color: var(--yellow); font-family: "Work Sans", sans-serif; font-weight: 500; font-size: 33px; letter-spacing: 1px; }
  .tagline { position: absolute; top: 210px; left: 0; width: 100%; text-align: center; color: var(--white); font-family: "Work Sans", sans-serif; font-size: 12px; letter-spacing: 0.5px; }
  .welcome { position: absolute; top: 247px; left: 0; width: 100%; text-align: center; color: var(--white); font-family: "Work Sans", sans-serif; font-weight: 600; font-size: 11px; letter-spacing: 2.5px; }
  .intro { position: absolute; top: 273px; left: 0; width: 100%; text-align: center; color: var(--white); font-family: "Work Sans", sans-serif; font-weight: 500; font-size: 10.5px; line-height: 13px; letter-spacing: 0.8px; }
  .cta { position: absolute; left: 367px; top: 325px; width: 106px; height: 28px; background: var(--button); color: var(--white); font-size: 10px; font-weight: 600; display: flex; align-items: center; justify-content: center; box-shadow: 0 2px 4px rgba(0,0,0,0.3); }
  .social { position: absolute; left: 44px; top: 362px; width: 24px; height: 24px; border: 1.3px solid var(--white); border-radius: 50%; }
  .legal { position: absolute; top: 391px; color: var(--white); font-size: 9.5px; }

  .section-title { position: absolute; left: 0; width: 100%; text-align: center; font-family: "Work Sans", sans-serif; color: var(--heading); }
  .products-title { top: 507px; font-weight: 700; font-size: 20px; letter-spacing: 4px; }
  .products-sub { top: 533px; font-size: 12.5px; font-weight: 400; letter-spacing: 1.2px; color: #2a1a10; }

  .card { position: absolute; top: 581px; width: 211px; height: 318px; background: var(--card); box-shadow: 0 1px 4px rgba(0,0,0,0.15); }
  .card-image { height: 133px; width: 100%; }
  .card-title { margin: 19px 0 0 26px; font-family: "Work Sans", sans-serif; font-weight: 500; font-size: 18.5px; line-height: 21px; color: var(--brown); letter-spacing: 0.8px; }
  .card-text { margin: 14px 18px 0 27px; font-size: 6.6px; line-height: 11.4px; color: var(--text); }
  .card-button { position: absolute; left: 26px; top: 268px; width: 109px; height: 22px; border: 1.5px solid var(--brown); color: var(--brown); font-size: 9.5px; font-weight: 600; display: flex; align-items: center; justify-content: center; }

  .arrow { position: absolute; top: 705px; width: 26px; height: 26px; border-radius: 50%; background: var(--white); box-shadow: 0 1px 4px rgba(0,0,0,0.35); }
  .dots { position: absolute; top: 914px; left: 423px; display: flex; gap: 3px; }
  .dot { width: 8px; height: 8px; border-radius: 50%; border: 1px solid var(--heading); }
  .dot.on { background: var(--heading); }
  .divider { position: absolute; top: 946px; left: 0; width: 100%; height: 1px; background: var(--line); }

  .projects-title { position: absolute; left: 56px; top: 995px; font-family: "Work Sans", sans-serif; font-weight: 700; font-size: 20px; line-height: 25px; letter-spacing: 4px; color: var(--heading); }
  .projects-text { position: absolute; left: 55px; top: 1061px; width: 290px; font-size: 9.3px; line-height: 16px; color: var(--text); }
  .photo { position: absolute; }
</style>
</head>
<body>
<div class="page">
  <nav class="nav">
    <a class="active" style="left:45px">Startseite</a>
    <a style="left:140px">Produkte</a>
    <a style="left:245px">Abgeschlossene Projekte</a>
    <a style="left:421px">Wer wir sind</a>
    <a style="left:737px">Kontakt</a>
  </nav>

  <header class="hero">
    <div class="hero-overlay" role="img" aria-label="Foto: Tischler sägt Holz zwischen Hobelspänen"></div>
    <div class="brand">RAHMENWERK</div>
    <div class="tagline">FENSTER HAUSTÜREN SONNENSCHUTZ</div>
    <div class="welcome">WILLKOMMEN</div>
    <div class="intro">Verkauf und Einbau von Fenstern, Haustüren, Rollläden,<br>Raffstore, Markisen, Insektenschutzgitter, Plissees</div>
    <div class="cta">Kontaktieren</div>
    <div class="social"></div>
    <span class="legal" style="left:654px">Impressum</span>
    <span class="legal" style="left:741px">Datenschutz</span>
  </header>

  <h2 class="section-title products-title">ALLE PRODUKTE IM ÜBERBLICK</h2>
  <p class="section-title products-sub">Klicken Sie sich durch unser breites Sortiment.</p>

  <div class="arrow" style="left:29px">
    <svg width="26" height="26" viewBox="0 0 26 26"><path d="M16 8 L9 13 L16 18 Z" fill="#c8c8c8"/></svg>
  </div>
  <div class="arrow" style="left:784px">
    <svg width="26" height="26" viewBox="0 0 26 26"><path d="M10 8 L17 13 L10 18 Z" fill="#c8c8c8"/></svg>
  </div>

  <article class="card" style="left:74px">
    <div class="card-image" role="img" aria-label="Foto: Handwerker mit Helm montiert ein Fenster" style="background:linear-gradient(90deg,#8d7f75,#d9d9d9)"></div>
    <h3 class="card-title">Einbau<br>von Fenstern</h3>
    <p class="card-text">Lorem ipsum dolor sit amet, consectetuer adipiscing elit, sed diam nonummy nibh euismod tincidunt ut laoreet dolore magna aliquam erat volutpat. Ut wm ipsum dolor sit amet, consectetuer adipiscing elit,</p>
    <div class="card-button">Mehr erfahren</div>
  </article>

  <article class="card" style="left:315px">
    <div class="card-image" role="img" aria-label="Foto: Holzhaustür an einem modernen Hauseingang" style="background:linear-gradient(90deg,#6f6a64,#8a4a2a 45%,#d6d3cf)"></div>
    <h3 class="card-title">Einbau<br>von Haustüren</h3>
    <p class="card-text">Lorem ipsum dolor sit amet, consectetuer adipiscing elit, sed diam nonummy nibh euismod tincidunt ut laoreet dolore magna aliquam erat volutpat. Ut wm ipsum dolor sit amet, consectetuer adipiscing elit,</p>
    <div class="card-button">Mehr erfahren</div>
  </article>

  <article class="card" style="left:554px">
    <div class="card-image" role="img" aria-label="Foto: Mann telefoniert vor Fenster mit Rollo" style="background:linear-gradient(90deg,#9aa6b8,#efe6d8)"></div>
    <h3 class="card-title">Einbau<br>von Rolläden</h3>
    <p class="card-text">Lorem ipsum dolor sit amet, consectetuer adipiscing elit, sed diam nonummy nibh euismod tincidunt ut laoreet dolore magna aliquam erat volutpat. Ut wm ipsum dolor sit amet, consectetuer adipiscing elit,</p>
    <div class="card-button">Mehr erfahren</div>
  </article>

  <div class="dots"><span class="dot on"></span><span class="dot"></span><span class="dot"></span></div>
  <div class="divider"></div>

  <h2 class="projects-title">UNSERE<br>ABGESCHLOSSENEN PROJEKTE</h2>
  <p class="projects-text">Lorem ipsum dolor sit amet, consectetuer adipiscing elit, sed diam nonummy nibh euismod tincidunt ut laoreet dolore magna aliquam erat volutpat. Ut wisi enim ad minim veniam, quis nostrud</p>

  <div class="photo" role="img" aria-label="Foto: Schwarze Haustür neben Klinkerwand" style="left:536px;top:974px;width:265px;height:176px;background:linear-gradient(90deg,#5a5a5a,#2a2a2a 45%,#6b5a50 70%,#b59a7a)"></div>
  <div class="photo" role="img" aria-label="Foto: Helles Wohnzimmer mit großen Fenstern" style="left:354px;top:1107px;width:231px;height:60px;background:linear-gradient(90deg,#bdbab4,#e6e3de)"></div>
  <div class="photo" role="img" aria-label="Foto: Raum mit Plissees" style="left:56px;top:1140px;width:246px;height:30px;background:linear-gradient(90deg,#e6dcc6,#cbbd9f)"></div>
</div>
</body>
</html>
```